Lumra Learning Web Design Project

Who We are:
Lumra Learning is education information portal/ magazine, providing information about the Chinese and International education markets. Our aim is to help school principals improve there curriculum, and parents in understanding this curriculum.

Project Brief:
The site will include education news updates, educational services, curriculum developments and overseas study. We hope the site represents the cross cultural bridge between the west and east. The site will cover both the Sciences and Arts.

Note:
The logo design competition is also underway so we only need the website design

What We want:
This competition is for Design only no coding!
Design a home page based on Template 1,2 or 3. I only need to select one.
The design of an article page.

Optional
Design a Parvex Shutters metro style splash page.

Sites We like:
http://www.qv.com.cn/tonguebridge/default.aspx
http://www.dailyuniversitybulletin.co.uk/
http://kptz.sinocraftlearn.net/

Template Explanations:
Template 1-
The main information has a dynamic sliding category view that when clicked displays the relevant info.
In addition to the main upper menu it also has a left hand sliding menu that pops out on click or gesture

Template 2-
Has limited number of Articles most of the menus are drop downs from the top menu

Template 3-
No Top menu

Target Market(s)

Teachers, principals and parents

Industry/Entity Type

Education

Requirements
Should not have
• kindergarten preschool feel

```html
<!DOCTYPE html>
<html lang="fr">
<head>
<meta charset="utf-8">
<title>Lumra Learning</title>
<link href="https://fonts.googleapis.com/css2?family=Play:wght@400;700&family=Ubuntu:wght@400;500;700&display=swap" rel="stylesheet">
<style>
:root{
  --bg:#2a2a2a;--panel:#fff;--footer:#2f2f2f;--red:#c4161c;--blue-title:#1b5fa6;
  --heading:#7a2a6a;--text:#6a6a6a;--card:#f4f4f4;--meta:#e7e5e1;
  --nav1:#d24f8a;--nav2:#efb32b;--nav3:#50b848;--nav4:#27a6df;--nav5:#9666b6;--nav6:#8b2273;--nav7:#b47935;
}
*{box-sizing:border-box;margin:0;padding:0}
html,body{width:1200px;height:2239px;overflow:hidden}
body{background:var(--bg);font-family:"Ubuntu",sans-serif;position:relative}
.abs{position:absolute}
.header{left:100px;top:19px;width:1000px;height:148px;background:var(--panel)}
.brand{left:20px;top:92px;display:flex;align-items:center;gap:8px;font:700 20px "Play",sans-serif;color:var(--red)}
.brand .dot{width:14px;height:14px;border-radius:50%;background:#1d5aa5}
.search{left:616px;top:54px;width:320px;height:36px;border:1px solid #ddd;font-size:11px;font-style:italic;color:#aaa;padding:11px 12px}
.search-btn{left:940px;top:54px;width:38px;height:36px;background:var(--red)}
.main{left:100px;top:178px;width:1000px;height:1717px;background:var(--panel)}
.nav{left:110px;top:188px;width:230px}
.nav a{display:flex;height:71px;color:#fff;text-decoration:none;font:400 19px "Play",sans-serif;align-items:center}
.nav .ic{width:60px;height:71px;background:rgba(0,0,0,.18);display:flex;align-items:center;justify-content:center}
.nav span{padding-left:16px}
.social{left:114px;top:703px;display:flex;gap:26px}
.social i{display:block;width:22px;height:22px;border-radius:50%}
.slider{left:351px;top:188px;width:570px;height:300px;background:linear-gradient(90deg,#3a4a6a 0%,#5a5a60 40%,#2e2a28 100%)}
.slider h2{position:absolute;left:209px;top:28px;width:350px;font:700 31px/38px "Play",sans-serif;color:#fff}
.readmore{position:absolute;left:440px;top:121px;width:100px;height:36px;background:var(--red);color:#fff;font:700 16px/36px "Play",sans-serif;text-align:center;border:2px solid #e24047}
.sec-head{left:351px;width:570px;height:30px;display:flex;align-items:center}
.sec-head .pill{width:35px;height:20px;background:var(--red);border-radius:10px 0 0 10px}
.sec-head h3{font:400 24px "Play",sans-serif;color:var(--heading);padding:0 14px 0 6px}
.sec-head .bar{flex:1;height:20px;background:var(--red);border-radius:0 10px 10px 0}
.card{width:282px;background:var(--card);border:1px solid #ececec}
.card .ph{margin:10px 10px 0;height:125px}
.card h4{margin:12px 10px 0;font:500 13.5px/18px "Ubuntu",sans-serif;color:var(--blue-title);text-transform:uppercase}
.card p{margin:8px 10px 0;font-size:11.5px;line-height:20px;color:var(--text)}
.card .meta{position:absolute;left:0;bottom:0;width:100%;height:32px;background:var(--meta);display:flex;align-items:center;gap:18px;padding-left:12px;font-size:12px;color:#333}
.meta span{display:flex;align-items:center;gap:5px}
.date{margin:6px 10px 0;font-size:11px;color:var(--red);display:flex;gap:5px;align-items:center}
.viewall{width:66px;height:26px;background:#1e4f86;border:1px solid #3f77b2;border-radius:4px;color:#fff;font-size:12px;text-align:center;line-height:24px}
.ad{left:931px;width:160px}
.ad1{top:188px;height:461px;background:linear-gradient(#0b3c7a,#0a2850);color:#fff;padding:20px 10px}
.ad1 h5{font:700 27px/28px "Ubuntu",sans-serif}
.ad1 p{font-size:10px;line-height:15px;text-align:center;margin-top:10px}
.ad1-ph{position:absolute;left:30px;top:180px;width:110px;height:280px;background:radial-gradient(circle at 50% 30%,#7fb8e6,#16457f 60%,#0a2850)}
.ad-org{top:657px;height:62px;background:#fff;display:flex;align-items:center;gap:8px;padding-left:10px;font:700 11px/13px "Ubuntu",sans-serif;color:#333}
.ad-org i{width:24px;height:24px;background:#555;border-radius:50%}
.ad-cta{top:728px;height:59px;background:#111;color:#fff;font-size:12px;line-height:15px;text-align:center;padding-top:14px;letter-spacing:1px}
.ad2{top:797px;height:600px;background:linear-gradient(#1aa6e0 0%,#1aa6e0 55%,#3fb54a 70%,#36a848 100%);text-align:center;color:var(--red);font:700 20px/26px "Ubuntu",sans-serif;padding-top:18px}
.ad2 .name{color:#f47a20;font-size:22px}
.ad2 .msg{margin-top:20px;color:#d00}
.ad2 .art{position:absolute;left:10px;top:260px;width:140px;height:320px;background:linear-gradient(#2a8fd0,#4cb050);border-radius:6px}
.ad3{top:1407px;height:438px;background:#0c1a36}
.ad3 .top{height:50px;background:#1870b8;color:#fff;font-size:12px;padding:18px 10px}
.ad3 h5{background:#1c5ca3;color:#fff;text-align:center;font:700 23px/25px "Ubuntu",sans-serif;padding:4px 0 6px}
.ad3 .red{background:#d8161c;color:#fff;font-size:12.5px;line-height:15px;text-align:center;padding:10px 2px}
.ad3 .art{height:222px;background:radial-gradient(ellipse at 50% 45%,#3a8ae0,#0c1a36 70%)}
.footer{left:100px;top:1918px;width:1000px;height:298px;background:var(--footer)}
.fcol{top:33px}
.fcol h6{font:400 15px "Play",sans-serif;color:#ddd;margin-bottom:18px}
.fcol a{display:block;font-size:11px;line-height:21px;color:#999;text-decoration:underline}
.fsoc{display:flex;gap:14px}
.fsoc i{width:32px;height:32px;background:#2a7bbf}
.newsletter{display:flex;margin-top:2px}
.newsletter .in{width:180px;height:30px;background:#222;font-size:10px;font-style:italic;color:#666;padding:9px 10px}
.newsletter .btn{width:84px;height:30px;background:var(--red);color:#fff;font-size:12px;line-height:30px;text-align:center}
.frule{left:19px;top:242px;width:962px;height:1px;background:#444}
.copy{left:19px;top:265px;font-size:11px;color:#999}
</style>
</head>
<body>
<header class="abs header">
  <div class="abs brand"><i class="dot"></i>Lumra Learning</div>
  <div class="abs search">Please enter your search</div>
  <div class="abs search-btn"><svg width="38" height="36"><circle cx="18" cy="17" r="6" fill="none" stroke="#fff" stroke-width="2.5"/><line x1="22" y1="21" x2="26" y2="25" stroke="#fff" stroke-width="2.5"/></svg></div>
</header>

<div class="abs main"></div>

<nav class="abs nav">
  <a style="background:var(--nav1)"><div class="ic"><svg width="30" height="28"><path d="M3 14L15 3l12 11M7 11v14h16V11" fill="none" stroke="#fff" stroke-width="2.5"/></svg></div><span>Home</span></a>
  <a style="background:var(--nav2)"><div class="ic"><svg width="32" height="26"><ellipse cx="12" cy="10" rx="10" ry="7" fill="#fff"/><ellipse cx="22" cy="16" rx="9" ry="6" fill="none" stroke="#fff" stroke-width="2"/></svg></div><span>About Us</span></a>
  <a style="background:var(--nav3)"><div class="ic"><svg width="30" height="30"><path d="M5 25L25 5M5 5l20 20" stroke="#fff" stroke-width="4"/></svg></div><span>Service</span></a>
  <a style="background:var(--nav4)"><div class="ic"><svg width="24" height="30"><path d="M3 2h12l6 6v20H3z" fill="none" stroke="#fff" stroke-width="2"/><path d="M7 14h10M7 19h10" stroke="#fff" stroke-width="2"/></svg></div><span>New &amp; Event</span></a>
  <a style="background:var(--nav5)"><div class="ic"><svg width="32" height="26"><rect x="2" y="2" width="28" height="22" fill="none" stroke="#fff" stroke-width="2"/><path d="M2 8h28M6 13h8M6 18h8M17 13h9v7h-9z" stroke="#fff" stroke-width="2" fill="none"/></svg></div><span>Blog</span></a>
  <a style="background:var(--nav6)"><div class="ic"><svg width="30" height="30"><rect x="3" y="3" width="24" height="16" fill="#fff"/><path d="M15 19v8M9 28l6-6 6 6" stroke="#fff" stroke-width="2" fill="none"/></svg></div><span>Lumra Learning</span></a>
  <a style="background:var(--nav7)"><div class="ic"><svg width="28" height="28"><path d="M6 3l5 5-3 4c2 4 5 7 9 9l4-3 5 5-4 4C12 26 2 16 2 7z" fill="#fff"/></svg></div><span>Contact Us</span></a>
</nav>
<div class="abs social"><i style="background:#c9445a"></i><i style="background:#e8a928"></i><i style="background:#4cae3c"></i><i style="background:#2895d6"></i><i style="background:#7a3f98"></i></div>

<section class="abs slider" role="img" aria-label="Smiling student holding a red folder in a library">
  <h2>Contrairement à unei nion répandue</h2>
  <div class="readmore">Read More</div>
</section>

<div class="abs sec-head" style="top:505px"><i class="pill"></i><h3>Latest Articles</h3><i class="bar"></i></div>

<article class="abs card" style="left:351px;top:540px;height:340px"><div class="ph" role="img" aria-label="Student with glasses outdoors" style="background:linear-gradient(135deg,#6b7a5a,#b89a86)"></div><h4>Plusieurs variations de Lorem Ipsum peuvent être trouvées ici ou.</h4><p>Le Lorem Ipsum est simplement du faux texte employé dans la composition et la mise en page avant impressionLe Lorem Ipsum est le faux texte standard.</p><div class="meta"><span><svg width="12" height="12"><circle cx="6" cy="3.5" r="3" fill="#c4161c"/><path d="M0 12c0-4 12-4 12 0z" fill="#c4161c"/></svg>By Admin</span><span><svg width="12" height="12"><circle cx="6" cy="6" r="5" fill="#c4161c"/><path d="M6 3v3h2" stroke="#fff" fill="none"/></svg>June 24, 2013</span></div></article>
<article class="abs card" style="left:642px;top:540px;height:340px"><div class="ph" role="img" aria-label="Two students reading together" style="background:linear-gradient(135deg,#c9a04a,#4a5a3a)"></div><h4>Ensemble des morceaux de texte pour réaliser un livre spécimen de.</h4><p>Contrairement à une opinion répandue, le Lorem Ipsum n'est pas simplement du texte aléatoire. Il trouve ses racines dans une oeuvre de la.</p><div class="meta"><span><svg width="12" height="12"><circle cx="6" cy="3.5" r="3" fill="#c4161c"/><path d="M0 12c0-4 12-4 12 0z" fill="#c4161c"/></svg>By Admin</span><span><svg width="12" height="12"><circle cx="6" cy="6" r="5" fill="#c4161c"/><path d="M6 3v3h2" stroke="#fff" fill="none"/></svg>June 24, 2013</span></div></article>
<article class="abs card" style="left:351px;top:888px;height:340px"><div class="ph" role="img" aria-label="Student with glasses outdoors" style="background:linear-gradient(135deg,#6b7a5a,#b89a86)"></div><h4>Plusieurs variations de Lorem Ipsum peuvent être trouvées ici ou.</h4><p>Le Lorem Ipsum est simplement du faux texte employé dans la composition et la mise en page avant impressionLe Lorem Ipsum est le faux texte standard.</p><div class="meta"><span><svg width="12" height="12"><circle cx="6" cy="3.5" r="3" fill="#c4161c"/><path d="M0 12c0-4 12-4 12 0z" fill="#c4161c"/></svg>By Admin</span><span><svg width="12" height="12"><circle cx="6" cy="6" r="5" fill="#c4161c"/><path d="M6 3v3h2" stroke="#fff" fill="none"/></svg>June 24, 2013</span></div></article>
<article class="abs card" style="left:642px;top:888px;height:340px"><div class="ph" role="img" aria-label="Two students reading together" style="background:linear-gradient(135deg,#c9a04a,#4a5a3a)"></div><h4>Ensemble des morceaux de texte pour réaliser un livre spécimen de.</h4><p>Contrairement à une opinion répandue, le Lorem Ipsum n'est pas simplement du texte aléatoire. Il trouve ses racines dans une oeuvre de la.</p><div class="meta"><span><svg width="12" height="12"><circle cx="6" cy="3.5" r="3" fill="#c4161c"/><path d="M0 12c0-4 12-4 12 0z" fill="#c4161c"/></svg>By Admin</span><span><svg width="12" height="12"><circle cx="6" cy="6" r="5" fill="#c4161c"/><path d="M6 3v3h2" stroke="#fff" fill="none"/></svg>June 24, 2013</span></div></article>
<div class="abs viewall" style="left:852px;top:1240px">View All</div>

<div class="abs sec-head" style="top:1281px"><i class="pill"></i><h3>Latest News</h3><i class="bar"></i></div>

<article class="abs card" style="left:351px;top:1316px;height:257px"><div class="ph" role="img" aria-label="Student reading a book by shelves" style="background:linear-gradient(135deg,#8a8a8a,#c8b49a)"></div><h4>Plusieurs variations de Lorem Ipsum peuvent</h4><div class="date"><svg width="10" height="10"><circle cx="5" cy="5" r="4.5" fill="#c4161c"/></svg>June 24, 2013</div><p>Le Lorem Ipsum est simplement du faux texte employé dans.</p></article>
<article class="abs card" style="left:642px;top:1316px;height:257px"><div class="ph" role="img" aria-label="Students talking in a group" style="background:linear-gradient(135deg,#7a4a8a,#d8b8a0)"></div><h4>Plusieurs variations de Lorem Ipsum peuvent</h4><div class="date"><svg width="10" height="10"><circle cx="5" cy="5" r="4.5" fill="#c4161c"/></svg>June 24, 2013</div><p>Le Lorem Ipsum est simplement du faux texte employé dans.</p></article>
<article class="abs card" style="left:351px;top:1585px;height:261px"><div class="ph" role="img" aria-label="Student studying with books" style="background:linear-gradient(135deg,#5a4a40,#b89a80)"></div><h4>Plusieurs variations de Lorem Ipsum peuvent</h4><div class="date"><svg width="10" height="10"><circle cx="5" cy="5" r="4.5" fill="#c4161c"/></svg>June 24, 2013</div><p>Le Lorem Ipsum est simplement du faux texte employé dans.</p></article>
<article class="abs card" style="left:642px;top:1585px;height:261px"><div class="ph" role="img" aria-label="Students sharing a phone" style="background:linear-gradient(135deg,#3a3030,#c8403a)"></div><h4>Plusieurs variations de Lorem Ipsum peuvent</h4><div class="date"><svg width="10" height="10"><circle cx="5" cy="5" r="4.5" fill="#c4161c"/></svg>June 24, 2013</div><p>Le Lorem Ipsum est simplement du faux texte employé dans.</p></article>
<div class="abs viewall" style="left:852px;top:1857px">View All</div>

<aside class="abs ad ad1"><h5>MAKE YOUR BUSINESS SMARTER.</h5><p>Northfield's newest resource helps you build a workforce that's well-trained and adaptable to your changing needs.</p><div class="ad1-ph" role="img" aria-label="Hand touching a glowing screen"></div></aside>
<div class="abs ad ad-org"><i></i>NORTHFIELD<br>CAREER<br>COLLEGE</div>
<div class="abs ad ad-cta">CLICK TO<br>LEARN MORE</div>
<aside class="abs ad ad2"><div class="name">Brightleaf Kids</div><div class="msg">Reading makes my heart feel SUPER HAPPY!</div><div class="art" role="img" aria-label="Cartoon character illustration on green grass"></div></aside>
<aside class="abs ad ad3"><div class="top">Spine Relief Center</div><h5>BACK PAIN GOT YOU DOWN?</h5><div class="red">WIPE OUT YOUR BACK PAIN IN 2 DAYS. GET YOUR FREE BACK PAIN ADVISORY!</div><div class="art" role="img" aria-label="Illustration of a human spine"></div></aside>

<footer class="abs footer">
  <div class="abs fcol" style="left:19px"><h6>Company</h6><a>Contrairement</a><a>Opinion répandue</a><a>Pas simplement du</a><a>Texte aléatoire</a></div>
  <div class="abs fcol" style="left:193px"><h6>Dictionnaire de</h6><a>Plusieurs variations</a><a>De Lorem Ipsum</a><a>Vent être</a></div>
  <div class="abs fcol" style="left:376px"><h6>Trouvées ici ou</h6><a>Siècle est reproduit</a><a>Dessous pour les</a><a>CurieuxPlusieurs varia-</a><a>tions</a><a>De Lorem Ipsum</a></div>
  <div class="abs fcol" style="left:554px"><h6>Embarassantes</h6><a>L'extrait standard</a><a>Utilisé depuis</a><a>Siècle est reproduit</a><a>Dessous pour les</a><a>Curieux</a><a>Vous voulez utiliser</a><a>Passage du Lorem</a></div>
  <div class="abs fcol" style="left:718px"><h6>Stay updates on our Socail Network</h6><div class="fsoc"><i></i><i></i><i></i></div><h6 style="margin-top:22px">Join Our Newsletter</h6><div class="newsletter"><div class="in">Enter your email address</div><div class="btn">Subscribe</div></div></div>
  <div class="abs frule"></div>
  <div class="abs copy">© Copyrights 2013 All rights Reserved</div>
</footer>
</body>
</html>
```